GTP biz card

We need a business card design for our new company based in Los Angeles called "Gold Tide Pictures". We develop film and television projects. We work with investors, financiers, film production companies, film distribution and sales companies as well as studios. We would like to incorporate our logo (see attached) on a two-sided card. We need to include: name and title, address, phone, email and company website.

Target Market(s)

Business, financial and studio clients

Industry/Entity Type

Business

Contact Information for Business Card

Two-sided. We are thinking of the logo on one side and the information on the back. Please feel free to be creative! Thanks.

Requirements
Must have
• Please include the following text information, excluding the "CAPS CATEGORY:" and please allow the ability for us to change the name, title and email address for each company employee):
• NAME & TITLE:
• Neil Parker
• Managing Partner
• COMPANY NAME:
• GOLD TIDE PICTURES (please use existing logo)
• COMPANY ADDRESS:
• KTW Studio Park
• 2250 Halverd Street
• Harbor Wing, 4th Floor
• Manhattan Beach, CA 90412
• COMPANY PHONE NUMBER:
• 310-555-0148
• COMPANY WEBSITE ADDRESS:
• www.goldtidepicturesgroup.example
• EMAIL ADDRESS: (only one per card)
• peter@goldtidepicturesgroup.example
• bingo@goldtidepicturesgroup.example
• neil@goldtidepicturesgroup.example

```html
<!DOCTYPE html>
<html lang="en">
<head>
<meta charset="utf-8">
<title>Gold Tide Pictures – Business Card</title>
<link rel="stylesheet" href="https://fonts.googleapis.com/css2?family=Play:wght@400;700&display=swap">
<style>
  :root {
    --canvas: #ebebeb;
    --card-dark: #231f20;
    --text-light: #ffffff;
    --brand-blue: #1aa9dc;
    --mark-fill: #0c7fae;
    --shadow: rgba(0, 0, 0, 0.55);
  }
  * { box-sizing: border-box; margin: 0; padding: 0; }
  html, body {
    width: 1200px; height: 1000px; overflow: hidden;
    background: var(--canvas);
    font-family: "Play", sans-serif;
  }
  .canvas { position: relative; width: 1200px; height: 1000px; }
  .card {
    position: absolute; left: 329px; width: 543px; height: 318px;
    background: var(--card-dark);
    box-shadow: 12px 14px 14px var(--shadow);
    overflow: hidden;
  }
  .card--info { top: 128px; }
  .card--brand {
    top: 522px;
    background: linear-gradient(90deg,
      #231f20 0%, #2a272a 30%, #4a4e58 55%, #5f7ea4 78%,
      #2a86d0 82%, #8fb6e6 88%, #dbe7f7 95%, #ffffff 100%);
  }
  .contact {
    position: absolute; right: 49px; top: 46px;
    text-align: right; color: var(--text-light);
    font-size: 16px; line-height: 20px;
  }
  .contact strong { font-weight: 700; }
  .contact .block + .block { margin-top: 35px; }
  .contact .web { margin-top: 20px; }
  .brand-small {
    position: absolute; left: 40px; top: 104px; width: 146px;
    text-align: center;
  }
  .brand-small .mark { display: block; margin: 0 auto 8px; }
  .brand-name {
    color: var(--brand-blue); font-weight: 700; letter-spacing: 0.5px;
    white-space: nowrap;
  }
  .brand-small .brand-name { font-size: 12px; }
  .brand-large {
    position: absolute; left: 0; right: 0; top: 57px; text-align: center;
  }
  .brand-large .mark { display: block; margin: 0 auto 10px; }
  .brand-large .brand-name { font-size: 24px; letter-spacing: 1px; }
</style>
</head>
<body>
<main class="canvas">
  <section class="card card--info" aria-label="Card front: contact details">
    <div class="brand-small">
      <svg class="mark" width="72" height="72" viewBox="0 0 72 72" aria-hidden="true">
        <circle cx="36" cy="36" r="36" fill="var(--mark-fill)"/>
      </svg>
      <div class="brand-name">GOLD TIDE PICTURES</div>
    </div>
    <div class="contact">
      <div class="block">
        <strong>Neil Parker</strong><br>
        <strong>Director</strong><br>
        neil@goldtidepicturesgroup.example
      </div>
      <div class="block">
        <strong>KTW Studio Park</strong><br>
        2250 Halverd Street<br>
        Harbor Wing, 4th Floor<br>
        Manhattan Beach, CA 90412<br>
        Phone: 310-555-0148
      </div>
      <div class="web">www.goldtidepicturesgroup.example</div>
    </div>
  </section>

  <section class="card card--brand" aria-label="Card back: company name">
    <div class="brand-large">
      <svg class="mark" width="132" height="132" viewBox="0 0 132 132" aria-hidden="true">
        <circle cx="66" cy="66" r="66" fill="var(--mark-fill)"/>
      </svg>
      <div class="brand-name">GOLD TIDE PICTURES</div>
    </div>
  </section>
</main>
</body>
</html>
```